New Innovative Counselling and psychotherapy Service needs Business Card design

Keep it simple and professional. On one side, just company name and logo (perhaps in all blue) and maybe a tag line.

On other side (all white) my name and Qualifications in centre

Industry/Entity Type

Health And Wellness

Contact Information for Business Card

Dara Whelby
Counsellor & Psychotherapist
BSc (Psychol.), BA, Dip. (Couns. & Psych.), PG.Cert (CBT), FGTrK, ONRE

I will also require Mobile no, Email and web site address of which I'll pass on to final designer.

Font styles to use
Sans Serif

Requirements
Must have
• My Logo Only and please use the colours in logo that is in it.
Should not have
• Any other images

```html
<!DOCTYPE html>
<html lang="en">
<head>
<meta charset="utf-8">
<title>Lumen Lane – Business Card</title>
<link rel="stylesheet" href="https://fonts.googleapis.com/css2?family=Montserrat:wght@300;400&family=Roboto:wght@400;700&display=swap">
<style>
  :root {
    --page-bg: #e9eaec;
    --card-white: #ffffff;
    --brand-blue: #4aa6dc;
    --brand-sky: #6cc3e6;
    --brand-teal: #7ccbb8;
    --brand-green: #8dcf6a;
    --icon-teal: #4bb39a;
    --icon-green: #7cc35c;
    --ink: #333438;
    --ink-soft: #55575c;
    --shadow: rgba(0, 0, 0, 0.12);
  }
  * { box-sizing: border-box; margin: 0; padding: 0; }
  html, body {
    width: 1200px;
    height: 726px;
    overflow: hidden;
    background: var(--page-bg);
  }
  .canvas {
    width: 1200px;
    height: 726px;
    display: flex;
    align-items: center;
    justify-content: center;
    gap: 50px;
  }
  .card {
    width: 520px;
    height: 297px;
    border-radius: 3px;
    box-shadow: 0 6px 18px var(--shadow);
    position: relative;
    overflow: hidden;
  }

  /* Front */
  .card--front {
    display: flex;
    align-items: center;
    justify-content: center;
  }
  .card-front__field {
    position: absolute;
    inset: 0;
    background: linear-gradient(120deg, var(--brand-sky) 0%, var(--brand-teal) 50%, var(--brand-green) 100%);
  }
  .card-front__name {
    position: relative;
    font-family: "Montserrat", sans-serif;
    font-weight: 400;
    font-size: 44px;
    letter-spacing: 1px;
    color: var(--card-white);
  }

  /* Back */
  .card--back {
    background: var(--card-white);
    display: flex;
    align-items: center;
    padding: 0 34px;
    gap: 28px;
  }
  .brand {
    display: flex;
    flex-direction: column;
    align-items: center;
    gap: 14px;
    width: 190px;
  }
  .brand__dot {
    width: 86px;
    height: 86px;
    border-radius: 50%;
    background: var(--brand-blue);
  }
  .brand__name {
    font-family: "Montserrat", sans-serif;
    font-weight: 400;
    font-size: 26px;
    color: var(--ink);
    white-space: nowrap;
  }
  .details {
    font-family: "Roboto", sans-serif;
    color: var(--ink-soft);
  }
  .details__name {
    font-weight: 700;
    font-size: 21px;
    color: var(--brand-blue);
    margin-bottom: 3px;
  }
  .details__role,
  .details__quals {
    font-size: 10.5px;
    line-height: 1.35;
  }
  .contact {
    list-style: none;
    margin-top: 22px;
    font-size: 13px;
    color: var(--ink);
  }
  .contact__item {
    display: flex;
    align-items: center;
    gap: 10px;
    line-height: 1.55;
  }
  .contact__icon { width: 12px; height: 12px; flex: none; }
</style>
</head>
<body>
<main class="canvas">
  <section class="card card--front" aria-label="Card front">
    <div class="card-front__field" role="img" aria-label="Soft blue to green gradient background"></div>
    <h1 class="card-front__name">Lumen Lane</h1>
  </section>

  <section class="card card--back" aria-label="Card back">
    <div class="brand">
      <span class="brand__dot"></span>
      <span class="brand__name">Lumen Lane</span>
    </div>
    <div class="details">
      <h2 class="details__name">Dara Whelby</h2>
      <p class="details__role">Counsellor &amp; Psychotherapist</p>
      <p class="details__quals">BSc (Psychol.), BA, Dip. (Couns. &amp; Psych.),<br>PG.Cert (CBT), FGTrK, ONRE</p>
      <ul class="contact">
        <li class="contact__item">
          <svg class="contact__icon" viewBox="0 0 12 12" aria-hidden="true"><path d="M2 1h2.5l1 2.5-1.3 1a6 6 0 0 0 3.3 3.3l1-1.3L11 7.5V10a1 1 0 0 1-1 1A9 9 0 0 1 1 2a1 1 0 0 1 1-1z" fill="var(--icon-teal)"/></svg>
          0845 316 2094
        </li>
        <li class="contact__item">
          <svg class="contact__icon" viewBox="0 0 12 12" aria-hidden="true"><rect x="0.5" y="2.5" width="11" height="7" rx="0.5" fill="var(--icon-green)"/><path d="M0.8 3 6 6.8 11.2 3" fill="none" stroke="#fff" stroke-width="1"/></svg>
          dara.w@LumenLane.com
        </li>
        <li class="contact__item">
          <svg class="contact__icon" viewBox="0 0 12 12" aria-hidden="true"><circle cx="6" cy="6" r="5" fill="none" stroke="var(--brand-blue)" stroke-width="1.2"/><ellipse cx="6" cy="6" rx="2.2" ry="5" fill="none" stroke="var(--brand-blue)" stroke-width="1"/><path d="M1 6h10" stroke="var(--brand-blue)" stroke-width="1"/></svg>
          www.LumenLane.com
        </li>
      </ul>
    </div>
  </section>
</main>
</body>
</html>
```